Business Card for Financial Asset Management Company

Now we are launching a new company based in Tokyo.
The company information is below;

Company Name: Velmora Advisory

Operations: Financial assets management, Proposing forming portfolio of assets, Consulting service, and advising to enhance your company's financial health

Corporate Colour: Japan Blue or Navy like below
http://stuweb.ax.tolvaric.edu/kpimra/pics/Shade/Mist-Shade-217.jpg

It's dark and deep, and will get to fit to our clients as our relationships last longer and longer.

Our images for this colour are "Japanese style" and "pride in our craftmanship" , and also "gentle".

Corporate Key Image: an order taker who is sincere, polite, but courageous

We don't have our logo yet so please feel free to put any symbol on your design.

Please do not hesitate about asking any questions.
Thank you :-)

Reason: We are still discussin on final decision. Thank you for your understanding.

```html
<!DOCTYPE html>
<html lang="en">
<head>
<meta charset="utf-8">
<title>Velmora Advisory — Business Card</title>
<link href="https://fonts.googleapis.com/css2?family=Open+Sans:wght@300;400;600;700&display=swap" rel="stylesheet">
<style>
  :root {
    --navy: #1b2e8c;
    --navy-deep: #15257a;
    --navy-light: #2740a6;
    --white: #ffffff;
    --paper: #eef0f4;
    --ink-soft: rgba(255,255,255,0.82);
  }
  * { box-sizing: border-box; margin: 0; padding: 0; }
  html, body { width: 1200px; height: 800px; overflow: hidden; }
  body {
    background: var(--paper);
    font-family: "Open Sans", Arial, sans-serif;
    position: relative;
  }
  .card {
    position: absolute;
    top: 250px;
    width: 520px;
    height: 300px;
    overflow: hidden;
    box-shadow: 0 6px 18px rgba(20,30,70,0.18);
  }
  .card-back { left: 60px; }
  .card-front { left: 620px; background: var(--white); }

  .card-fill {
    position: absolute; inset: 0;
    background: linear-gradient(170deg, var(--navy-deep), var(--navy) 55%, var(--navy-light));
  }
  .front-band {
    position: absolute; left: 0; right: 0; top: 120px; bottom: 0;
    background: linear-gradient(180deg, var(--navy), var(--navy-light));
  }

  .brand { display: flex; align-items: center; gap: 10px; }
  .brand-mark { width: 34px; height: 34px; border-radius: 50%; flex: none; }
  .brand-name { font-weight: 600; line-height: 1.05; }

  .card-back .brand {
    position: absolute; left: 0; right: 0; top: 62px;
    flex-direction: column; gap: 10px;
  }
  .card-back .brand-mark { background: var(--white); width: 40px; height: 40px; }
  .card-back .brand-name { color: var(--white); font-size: 26px; text-align: center; }

  .tagline {
    position: absolute; left: 0; right: 0; top: 206px;
    text-align: center; color: var(--white); font-size: 12.5px; letter-spacing: 0.2px;
  }
  .tagline-rule {
    position: absolute; left: 182px; width: 156px; top: 232px;
    height: 1px; background: var(--ink-soft);
  }
  .web {
    position: absolute; left: 0; right: 0; top: 244px;
    text-align: center; color: var(--ink-soft); font-size: 10.5px;
  }

  .card-front .brand { position: absolute; left: 36px; top: 30px; }
  .card-front .brand-mark { background: var(--navy); }
  .card-front .brand-name { color: var(--navy); font-size: 22px; }

  .contact {
    position: absolute; left: 80px; top: 146px;
    color: var(--white);
  }
  .contact-rule {
    position: absolute; left: 80px; top: 146px; width: 1px; height: 138px;
    background: var(--ink-soft);
  }
  .contact-body { padding-left: 16px; }
  .person-name { font-weight: 700; font-size: 19px; line-height: 1.3; }
  .person-role { font-size: 12.5px; margin-top: 2px; }
  .contact-lines { margin-top: 16px; font-size: 12px; font-weight: 300; line-height: 1.55; color: var(--ink-soft); }
</style>
</head>
<body>
  <section class="card card-back" aria-label="Business card back">
    <div class="card-fill" role="img" aria-label="Deep navy background with soft layered wave pattern"></div>
    <div class="brand">
      <span class="brand-mark"></span>
      <span class="brand-name">Velmora Advisory</span>
    </div>
    <p class="tagline">Financial Assets . Proposing Portfolio . Consulting Services</p>
    <span class="tagline-rule"></span>
    <p class="web">www.velmora-advisory.jp</p>
  </section>

  <section class="card card-front" aria-label="Business card front">
    <div class="front-band" role="img" aria-label="Navy band with soft layered wave pattern"></div>
    <div class="brand">
      <span class="brand-mark"></span>
      <span class="brand-name">Velmora Advisory</span>
    </div>
    <span class="contact-rule"></span>
    <div class="contact">
      <div class="contact-body">
        <p class="person-name">Emiko Tanabe</p>
        <p class="person-role">General Director</p>
        <div class="contact-lines">
          <p>emiko.tanabe@velmora-advisory.jp</p>
          <p>Tel. 090 555 2417 &nbsp;|&nbsp; Fax. 090 555 2418</p>
          <p>Suzunari Harbor Tower</p>
          <p>4-7, Suzunari 3-Chome, Chuo-ku, Tokyo 104-0071</p>
        </div>
      </div>
    </div>
  </section>
</body>
</html>
```